Business card for Crestline Bathrooms

Please design a business card for our bathroom renovation business. You can use my existing logo, but if you have an idea to modernize it, I would like to see it. Please see attached files first. I would like to use the blue and the orange theme. I like the concept of using the shower head in the logo. Please find following a design (or two) that I have been trying to create with my limited resources. That design was for a sign, but I was going to adopt it and use it as a business card as well. I like the concept of the water splash but I don’t think it “flows” nicely together with the logo. Another thought is that maybe creating the logo out of water splash could work and have a dramatic effect (like the water text and the butterfly picture attached with similar background instead of white). If the above doesn’t work I would like to see a modern simplified design. One of the attached files named as the unwanted business card has all the details that I want included in the business card. Please note that it is two sided.
Updates

I am very thankful for the designs that I have received, but they are very similar and only a couple of attempts to do something with the water splash as per my original brief. Modernizing the logo and having it made out of out of water splash with the orange as color accent could work and have a dramatic effect (like the water text and the butterfly picture attached with similar background instead of white). Please do not use the butterfly itself! This is just an example that images can be created out of water splash.

Contact Information for Business Card

all the details are on the unwonted business card file included

Colors
3176b5

Requirements
Nice to have
• Copied from the brief:
• ... maybe creating the logo out of water splash could work and have a dramatic effect (like the water text and the butterfly picture attached with similar background instead of white). Please do not use the butterfly itself!
Should not have
• I am getting designs with a butterfly. The butterfly picture was an example of creating something from a water splash. The butterfly itself has no association with anything other than the concept of creating a logo out of water splash. Sorry, I thought I was clear in the brief.

```html
<!DOCTYPE html>
<html lang="en">
<head>
<meta charset="utf-8">
<title>Crestline Bathrooms – Business Card</title>
<link rel="stylesheet" href="https://fonts.googleapis.com/css2?family=Roboto:wght@400;500&family=Short+Stack&display=swap">
<style>
  :root {
    --backdrop: #e3e3e3;
    --card-white: #f3f3f3;
    --navy: #173a63;
    --navy-deep: #112c4d;
    --water: #3176b5;
    --coral: #ea776b;
    --ink-light: #ffffff;
  }
  * { box-sizing: border-box; margin: 0; padding: 0; }
  html, body {
    width: 1200px; height: 960px; overflow: hidden;
    background: var(--backdrop);
    font-family: "Roboto", Arial, sans-serif;
  }
  .canvas { position: relative; width: 1200px; height: 960px; }

  .card {
    position: absolute;
    width: 600px; height: 344px;
    display: flex;
    background: var(--card-white);
  }
  .card--front { left: 314px; top: 113px; }
  .card--back  { left: 311px; top: 472px; }

  .brand-side {
    flex: 1;
    display: flex; align-items: center; justify-content: center;
  }
  .wordmark {
    display: flex; align-items: center; gap: 12px;
    color: var(--navy);
    font-family: "Roboto", Arial, sans-serif;
    font-weight: 500;
    font-size: 30px;
    line-height: 1.1;
  }
  .wordmark__dot {
    width: 22px; height: 22px; border-radius: 50%;
    background: var(--coral); flex: none;
  }

  /* front: contact panel */
  .contact-panel {
    position: relative;
    width: 306px; height: 100%;
  }
  .contact-panel__splash {
    position: absolute; inset: 0;
    background:
      radial-gradient(ellipse 70% 40% at 70% 85%, rgba(190,210,230,.75), rgba(49,118,181,0) 70%),
      radial-gradient(ellipse 60% 50% at 15% 10%, rgba(49,118,181,.6), rgba(49,118,181,0) 70%),
      linear-gradient(160deg, #24507f 0%, var(--navy) 45%, var(--navy-deep) 100%);
  }
  .contact-panel__text {
    position: absolute; left: 36px; top: 90px;
    color: var(--ink-light);
  }
  .contact-name {
    font-family: "Short Stack", "Comic Sans MS", cursive;
    color: var(--coral);
    font-size: 24px; letter-spacing: .5px;
    line-height: 1; margin-bottom: 10px;
  }
  .contact-address {
    font-size: 14.5px; line-height: 19px;
    margin-bottom: 9px;
  }
  .contact-list { list-style: none; }
  .contact-list li {
    display: flex; align-items: center; gap: 8px;
    font-size: 14.5px; line-height: 19px;
  }
  .contact-list svg { width: 14px; height: 14px; flex: none; fill: var(--coral); }

  /* back: services panel */
  .services-panel {
    width: 294px; height: 100%;
    background: var(--coral);
    color: var(--ink-light);
    padding: 45px 20px 0 34px;
    position: relative;
  }
  .services-list { list-style: none; }
  .services-list li {
    position: relative;
    padding-left: 17px;
    font-size: 14.5px; line-height: 19px;
    margin-bottom: 18px;
  }
  .services-list li::before {
    content: ""; position: absolute; left: 0; top: 6px;
    width: 6px; height: 6px; border-radius: 50%;
    background: var(--ink-light);
  }
  .member-badges {
    position: absolute; left: 36px; bottom: 42px;
    display: flex; align-items: center; gap: 16px;
  }
  .member-badge--square {
    width: 30px; height: 34px; border-radius: 4px; background: var(--ink-light);
  }
  .member-badges__divider { width: 1px; height: 36px; background: var(--ink-light); }
  .member-badge--wide {
    width: 116px; height: 26px; border-radius: 2px; background: var(--ink-light);
  }
</style>
</head>
<body>
<main class="canvas">

  <section class="card card--front" aria-label="Business card front">
    <div class="brand-side">
      <div class="wordmark"><span class="wordmark__dot"></span><span>Crestline<br>Bathrooms</span></div>
    </div>
    <div class="contact-panel">
      <div class="contact-panel__splash" role="img" aria-label="Photograph of water splashing and droplets on a deep blue background"></div>
      <div class="contact-panel__text">
        <p class="contact-name">Daniel Ostrowski</p>
        <p class="contact-address">PO Box 41<br>Kellerton 2740</p>
        <ul class="contact-list">
          <li><svg viewBox="0 0 16 16"><path d="M3.5 1l2.5 3-1.5 1.8a9 9 0 0 0 5.7 5.7L12 10l3 2.5-1.5 2.5C7 15 1 9 1 2.5z"/></svg>0400 555 218</li>
          <li><svg viewBox="0 0 16 16"><path d="M4 0h8a1 1 0 0 1 1 1v14a1 1 0 0 1-1 1H4a1 1 0 0 1-1-1V1a1 1 0 0 1 1-1zm1 2v10h6V2zm3 11a1 1 0 1 0 0 2 1 1 0 0 0 0-2z"/></svg>5550 7142</li>
          <li><svg viewBox="0 0 16 16"><path d="M1 3h14v1.2L8 9 1 4.2zm0 2.6 7 4.8 7-4.8V13H1z"/></svg>daniel@crestlinebathrooms.com.au</li>
          <li><svg viewBox="0 0 16 16"><path d="M8 1a7 7 0 1 0 0 14A7 7 0 0 0 8 1zm0 1.5c.8 0 1.8 2 2 4.7H6c.2-2.7 1.2-4.7 2-4.7zM6 8.8h4c-.2 2.7-1.2 4.7-2 4.7s-1.8-2-2-4.7z"/></svg>crestlinebathrooms.com.au</li>
        </ul>
      </div>
    </div>
  </section>

  <section class="card card--back" aria-label="Business card back">
    <div class="services-panel">
      <ul class="services-list">
        <li>Complete Bathroom Renovations<br>&amp; Remodelling</li>
        <li>Highly Skilled &amp;<br>Qualified Tradespeople</li>
        <li>Professional Service From<br>Concept To Completion</li>
        <li>All Work Guaranteed</li>
      </ul>
      <div class="member-badges" aria-label="Industry membership badges">
        <span class="member-badge--square"></span>
        <span class="member-badges__divider"></span>
        <span class="member-badge--wide"></span>
      </div>
    </div>
    <div class="brand-side">
      <div class="wordmark"><span class="wordmark__dot"></span><span>Crestline<br>Bathrooms</span></div>
    </div>
  </section>

</main>
</body>
</html>
```